Golf Tournament Flyer and Header Needed

Non-profit needs a flyer for their benefit golf tournament - "Wild Socks Benefit Golf Classic"

Target Market(s)

Design and Construction industry professionals

Industry/Entity Type

Design and Construction

Colors

Designer to choose colors to be used in the design.

Requirements
Must have
• Date: September 22, 2021, 8:00 AM Shotgun Start, Location: Brookmere Links. O-VardeX Logo
Nice to have
• Would like image of golfers in crazy pants incorporated.

```html
<!DOCTYPE html>
<html lang="en">
<head>
<meta charset="utf-8">
<title>Wild Socks Benefit Golf Classic</title>
<link href="https://fonts.googleapis.com/css2?family=Oswald:wght@500;600&family=Open+Sans:wght@700&family=Roboto+Condensed:wght@700&display=swap" rel="stylesheet">
<style>
  :root {
    --royal: #3451a6;
    --royal-deep: #2a3f93;
    --royal-light: #5a7fd0;
    --lime: #7cc142;
    --lime-deep: #5fa630;
    --navy-text: #2d3f99;
    --white: #ffffff;
  }
  html, body {
    margin: 0;
    padding: 0;
    width: 961px;
    height: 1200px;
    overflow: hidden;
    background: var(--white);
  }
  .flyer {
    display: block;
    width: 961px;
    height: 1200px;
  }
  .brand-name {
    font-family: "Open Sans", sans-serif;
    font-weight: 700;
    font-size: 34px;
    fill: var(--white);
  }
  .event-title {
    font-family: "Oswald", sans-serif;
    font-weight: 600;
    font-size: 84px;
    fill: var(--white);
    letter-spacing: 1px;
  }
  .event-subtitle {
    font-family: "Roboto Condensed", sans-serif;
    font-weight: 700;
    font-size: 29px;
    fill: var(--lime);
    letter-spacing: 0.5px;
  }
  .detail-text {
    font-family: "Open Sans", sans-serif;
    font-weight: 700;
    font-size: 30px;
    fill: var(--white);
  }
  .contact-heading {
    font-family: "Roboto Condensed", sans-serif;
    font-weight: 700;
    font-size: 25px;
    fill: var(--navy-text);
  }
  .contact-line {
    font-family: "Open Sans", sans-serif;
    font-weight: 700;
    font-size: 22px;
    fill: var(--white);
    letter-spacing: 0.5px;
  }
</style>
</head>
<body>
<svg class="flyer" viewBox="0 0 961 1200" xmlns="http://www.w3.org/2000/svg">
  <defs>
    <linearGradient id="bg-blue" x1="0" y1="0" x2="1" y2="1">
      <stop offset="0" stop-color="#3a5ab0"/>
      <stop offset="1" stop-color="var(--royal-deep)"/>
    </linearGradient>
    <linearGradient id="light-wedge" x1="0" y1="0" x2="1" y2="1">
      <stop offset="0" stop-color="#e9f0fb"/>
      <stop offset="1" stop-color="#7c9be0"/>
    </linearGradient>
    <linearGradient id="green-wedge" x1="0" y1="0" x2="1" y2="1">
      <stop offset="0" stop-color="var(--lime)"/>
      <stop offset="1" stop-color="var(--lime-deep)"/>
    </linearGradient>
    <linearGradient id="photo-top" x1="0" y1="0" x2="0" y2="1">
      <stop offset="0" stop-color="#8fb3d6"/>
      <stop offset="0.35" stop-color="#e8536f"/>
      <stop offset="0.7" stop-color="#4fb0a4"/>
      <stop offset="1" stop-color="#5f8a3e"/>
    </linearGradient>
    <linearGradient id="photo-bottom" x1="0" y1="0" x2="0" y2="1">
      <stop offset="0" stop-color="#a9cdeb"/>
      <stop offset="0.3" stop-color="#eef0f4"/>
      <stop offset="0.65" stop-color="#4d73c2"/>
      <stop offset="1" stop-color="#5c8a3b"/>
    </linearGradient>
  </defs>

  <!-- base -->
  <rect class="backdrop" width="961" height="1200" fill="url(#bg-blue)"/>

  <!-- light wedge at left -->
  <polygon class="light-wedge" points="0,520 0,700 300,820" fill="url(#light-wedge)" opacity="0.85"/>

  <!-- green corner -->
  <polygon class="green-corner" points="961,600 961,1200 490,1200" fill="url(#green-wedge)"/>

  <!-- faint diagonal stripes -->
  <g class="accent-stripes" stroke="#ffffff" stroke-opacity="0.12" stroke-width="3">
    <line x1="560" y1="700" x2="880" y2="620"/>
    <line x1="600" y1="730" x2="900" y2="655"/>
    <line x1="640" y1="760" x2="920" y2="690"/>
  </g>

  <!-- top right team photo -->
  <polygon class="photo photo--top" role="img" aria-label="Photo of four golfers in pink shirts and flamingo-print pants"
           points="239,0 961,0 961,583" fill="url(#photo-top)"/>

  <!-- bottom left team photo -->
  <polygon class="photo photo--bottom" role="img" aria-label="Photo of four golfers in white shirts and blue argyle pants"
           points="0,800 150,800 560,800 720,1200 0,1200" fill="url(#photo-bottom)"/>

  <!-- brand -->
  <g class="brand">
    <circle cx="53" cy="96" r="18" fill="var(--white)"/>
    <text class="brand-name" x="82" y="108">O-VardeX</text>
  </g>

  <!-- title -->
  <text class="event-title" x="31" y="250">WILD SOCKS</text>
  <text class="event-title" x="31" y="345">BENEFIT</text>

  <g class="subtitle">
    <line x1="30" y1="380" x2="115" y2="380" stroke="var(--lime)" stroke-width="2"/>
    <text class="event-subtitle" x="239" y="391" text-anchor="middle">GOLF CLASSIC</text>
    <line x1="363" y1="380" x2="450" y2="380" stroke="var(--lime)" stroke-width="2"/>
  </g>

  <!-- event details -->
  <g class="detail detail--date">
    <circle cx="137" cy="463" r="43" fill="var(--lime)" stroke="var(--white)" stroke-width="4"/>
    <rect x="117" y="446" width="40" height="36" rx="3" fill="none" stroke="var(--white)" stroke-width="3"/>
    <line x1="117" y1="456" x2="157" y2="456" stroke="var(--white)" stroke-width="3"/>
    <g fill="var(--white)">
      <rect x="123" y="462" width="5" height="5"/><rect x="134" y="462" width="5" height="5"/><rect x="145" y="462" width="5" height="5"/>
      <rect x="123" y="471" width="5" height="5"/><rect x="134" y="471" width="5" height="5"/><rect x="145" y="471" width="5" height="5"/>
    </g>
    <text class="detail-text" x="207" y="474">SEPTEMBER 22, 2021</text>
  </g>

  <g class="detail detail--time">
    <circle cx="205" cy="533" r="43" fill="var(--lime)" stroke="var(--white)" stroke-width="4"/>
    <circle cx="205" cy="533" r="21" fill="none" stroke="var(--white)" stroke-width="3"/>
    <polyline points="205,519 205,533 215,540" fill="none" stroke="var(--white)" stroke-width="3" stroke-linecap="round"/>
    <text class="detail-text" x="283" y="543">8:00 AM SHOTGUN START</text>
  </g>

  <g class="detail detail--location">
    <circle cx="279" cy="605" r="43" fill="var(--lime)" stroke="var(--white)" stroke-width="4"/>
    <path d="M279 584 a13 13 0 0 1 13 13 c0 10 -13 24 -13 24 s-13 -14 -13 -24 a13 13 0 0 1 13 -13 z" fill="var(--white)"/>
    <circle cx="279" cy="597" r="5" fill="var(--lime)"/>
    <text class="detail-text" x="340" y="616">LOCATION: BROOKMERE LINKS</text>
  </g>

  <!-- contact -->
  <g class="contact" text-anchor="end">
    <text class="contact-heading" x="938" y="1030">FOR MORE</text>
    <text class="contact-heading" x="938" y="1058">INFORMATION</text>
    <text class="contact-heading" x="938" y="1086">PLEASE CONTACT US</text>
    <text class="contact-line" x="905" y="1134">512-555-0147</text>
    <text class="contact-line" x="905" y="1173">www.O-VardeX.org</text>
  </g>
  <path class="icon-phone" d="M922 1118 l5 -2 l3 6 l-3 2 a12 12 0 0 0 5 5 l2 -3 l6 3 l-2 5 c-9 1 -17 -7 -16 -16 z" fill="var(--navy-text)"/>
  <g class="icon-web" fill="none" stroke="var(--navy-text)" stroke-width="2">
    <circle cx="930" cy="1165" r="10"/>
    <ellipse cx="930" cy="1165" rx="4" ry="10"/>
    <line x1="920" y1="1165" x2="940" y2="1165"/>
  </g>
</svg>
</body>
</html>
```